Casino with the 'highest winning percentage' needs a stationery design

This is for a casino in Colombo, Sri Lanka and we need a stationery design for business card, letter head and envelope.

Should be very professional, simple and elegant without fancy fonts

Reason: Not fully satisfied with the designs. Need more designs.

Business

• 1. card deck symbol 'CLUBS' in red, or black

2. name in BLOCK CAPITAL LETTERS

3. Preferred font colours are black, white or red

4. Prefer 'professional /elegant' fonts
• SHOULD NOT HAVE ANY OTHER SYMBOL EXCEPT 'CLUBS'

DO NOT PREFER ITALIC FONTS

```html
<!DOCTYPE html>
<html lang="en">
<head>
<meta charset="utf-8">
<title>Corvell's Entertainment — Stationery</title>
<link rel="stylesheet" href="https://fonts.googleapis.com/css2?family=Noto+Serif:wght@400;700&family=Open+Sans:wght@300;400&display=swap">
<style>
  :root {
    --ink: #1a1a1a;
    --red: #d7182a;
    --band-red: #e3202f;
    --paper: #ffffff;
    --paper-shade: #e9e9ea;
    --rule: #333333;
    --muted: #444444;
    --watermark: #f3e1e3;
    --stage: #ece9e4;
  }
  * { box-sizing: border-box; margin: 0; padding: 0; }
  html, body { width: 1200px; height: 509px; overflow: hidden; }
  body {
    position: relative;
    background: var(--stage);
    font-family: "Noto Serif", Georgia, serif;
    color: var(--ink);
  }
  .sheet, .envelope, .card {
    position: absolute;
    background: linear-gradient(135deg, var(--paper) 45%, var(--paper-shade) 100%);
    box-shadow: 0 1px 4px rgba(0,0,0,.25);
    overflow: hidden;
  }

  /* Brand name block */
  .brand { position: absolute; display: flex; align-items: center; gap: 6px; }
  .brand-dot { border-radius: 50%; background: var(--red); flex: none; }
  .brand-name {
    font-weight: 700; color: var(--ink); text-transform: uppercase;
    line-height: 1.3; letter-spacing: .2px;
  }

  /* Letterhead */
  .letterhead { left: 10px; top: 40px; width: 334px; height: 430px; }
  .letterhead .brand { left: 97px; top: 12px; }
  .brand-dot.md { width: 30px; height: 30px; }
  .brand-name.md { font-size: 11.5px; }
  .watermark {
    position: absolute; left: 101px; top: 150px; width: 130px; height: 130px;
    border-radius: 50%; background: var(--watermark);
  }
  .letter-footer {
    position: absolute; left: 0; right: 0; top: 415px; text-align: center;
    font-size: 5.4px; line-height: 1.55; color: var(--muted);
  }
  .letter-footer .company { color: var(--red); }
  .icon-dot {
    display: inline-block; width: 4px; height: 4px; border-radius: 50%;
    background: var(--red); vertical-align: middle; margin: 0 2px 0 4px;
  }

  /* Fax sheet */
  .fax { left: 382px; top: 40px; width: 333px; height: 430px; }
  .fax .brand { left: 13px; top: 12px; }
  .fax-contact {
    position: absolute; left: 240px; top: 6px; padding-left: 4px;
    border-left: 0.6px solid #999; font-size: 5.2px; line-height: 1.55; color: var(--muted);
  }
  .fax-contact .company { color: var(--red); }
  .fax-contact .icon-dot { margin-left: 0; }
  .fax-title {
    position: absolute; left: 12px; top: 98px;
    font-family: "Open Sans", Arial, sans-serif; font-weight: 400; font-size: 21px;
  }
  .fax-field {
    position: absolute; height: 10px; border-bottom: 0.8px solid var(--rule);
    font-family: "Open Sans", Arial, sans-serif; font-size: 6px; line-height: 8px;
  }
  .fax-field.left { left: 12px; width: 144px; }
  .fax-field.right { left: 182px; width: 115px; }
  .fax-options {
    position: absolute; left: 12px; top: 219px; width: 300px;
    display: flex; justify-content: space-between;
    font-family: "Open Sans", Arial, sans-serif; font-size: 6px;
  }
  .fax-options span { display: flex; align-items: center; gap: 5px; }
  .checkbox { width: 7px; height: 7px; border: 0.8px solid var(--rule); }
  .site {
    position: absolute; font-size: 6.4px; letter-spacing: 1px; color: var(--ink);
  }
  .fax .site { right: 8px; top: 414px; }
  .band { position: absolute; left: 0; bottom: 0; display: block; }

  /* Envelopes */
  .envelope.back { left: 820px; top: 8px; width: 372px; height: 166px; }
  .envelope.middle { left: 739px; top: 80px; width: 372px; height: 164px; }
  .flap { position: absolute; left: 0; top: 0; }
  .envelope.front { left: 778px; top: 154px; width: 373px; height: 166px; }
  .envelope.front .brand { left: 11px; top: 10px; }
  .envelope-address {
    position: absolute; left: 54px; top: 48px; font-size: 6.2px; line-height: 1.45;
  }
  .envelope.front .site { left: 54px; top: 148px; }

  /* Business cards */
  .card { width: 203px; height: 116px; top: 342px; }
  .card.face { left: 769px; }
  .card.face .brand { left: 30px; top: 12px; }
  .brand-dot.sm { width: 26px; height: 26px; }
  .brand-name.sm { font-size: 10px; }
  .card-company {
    position: absolute; right: 106px; top: 60px; text-align: right;
    font-size: 5.4px; line-height: 1.55;
  }
  .card-company .company { color: var(--red); font-weight: 700; font-size: 6px; margin-bottom: 4px; }
  .card-divider { position: absolute; left: 102px; top: 58px; width: 0.6px; height: 40px; background: #999; }
  .card-contact {
    position: absolute; left: 106px; top: 58px; font-size: 5.2px; line-height: 1.6; color: var(--muted);
  }
  .card-contact .icon-dot { margin-left: 0; }
  .card.reverse { left: 982px; }
  .card.reverse .brand { left: 30px; top: 28px; }
  .tagline {
    position: absolute; left: 0; right: 0; top: 88px; text-align: center;
    font-size: 6.4px; font-weight: 700; letter-spacing: .5px; color: var(--red);
  }
</style>
</head>
<body>

<section class="sheet letterhead" aria-label="Letterhead">
  <div class="brand">
    <span class="brand-dot md"></span>
    <div class="brand-name md">Corvell's<br>Entertainment</div>
  </div>
  <div class="watermark"></div>
  <footer class="letter-footer">
    <div><span class="company">CORVELL'S LIMITED</span> &nbsp;/&nbsp; 18, Lotus Garden Road, Colombo 01000, Sri Lanka</div>
    <div><span class="icon-dot"></span>+ 94 11 5550142 <span class="icon-dot"></span>+ 94 11 5550100 <span class="icon-dot"></span>info@corvellcolombo.com <span class="icon-dot"></span>www.corvellcolombo.com</div>
  </footer>
</section>

<section class="sheet fax" aria-label="Fax sheet">
  <div class="brand">
    <span class="brand-dot md"></span>
    <div class="brand-name md">Corvell's<br>Entertainment</div>
  </div>
  <div class="fax-contact">
    <div><span class="icon-dot"></span>+ 94 11 5550142</div>
    <div><span class="icon-dot"></span>+ 94 11 5550100</div>
    <div><span class="icon-dot"></span>info@corvellcolombo.com</div>
    <div class="company">CORVELL'S LIMITED</div>
    <div>18, Lotus Garden Road</div>
    <div>Colombo 01000, Sri Lanka</div>
  </div>
  <h1 class="fax-title">FAX</h1>
  <div class="fax-field left" style="top:136px">To :</div>
  <div class="fax-field right" style="top:136px">From :</div>
  <div class="fax-field left" style="top:154px">Fax :</div>
  <div class="fax-field right" style="top:154px">Pages :</div>
  <div class="fax-field left" style="top:172px">Phone :</div>
  <div class="fax-field right" style="top:172px">Date :</div>
  <div class="fax-field left" style="top:190px">Re :</div>
  <div class="fax-field right" style="top:190px">CC :</div>
  <div class="fax-options">
    <span><i class="checkbox"></i>Urgent</span>
    <span><i class="checkbox"></i>For Review</span>
    <span><i class="checkbox"></i>Please Comment</span>
    <span><i class="checkbox"></i>Please Reply</span>
    <span><i class="checkbox"></i>Please Recycle</span>
  </div>
  <div class="site">www.corvellcolombo.com</div>
  <svg class="band" width="333" height="8" viewBox="0 0 333 8">
    <polygon points="0,0 166,0 159,8 0,8" fill="var(--ink)"/>
    <polygon points="169,0 333,0 333,8 162,8" fill="var(--band-red)"/>
  </svg>
</section>

<section class="envelope back" aria-label="Envelope back, closed flap">
  <svg class="flap" width="372" height="166" viewBox="0 0 372 166">
    <path d="M0,0 H372 V20 Q372,30 352,38 L204,72 Q186,76 168,72 L20,38 Q0,30 0,20 Z" fill="var(--ink)"/>
    <circle cx="186" cy="44" r="14" fill="var(--red)"/>
  </svg>
</section>

<section class="envelope middle" aria-label="Envelope back, white flap">
  <svg class="flap" width="372" height="164" viewBox="0 0 372 164">
    <path d="M0,14 Q0,28 18,36 L168,78 Q186,83 204,78 L354,36 Q372,28 372,14" fill="none" stroke="var(--rule)" stroke-width="0.9"/>
    <circle cx="186" cy="48" r="14" fill="var(--red)"/>
  </svg>
</section>

<section class="envelope front" aria-label="Envelope front">
  <div class="brand">
    <span class="brand-dot md"></span>
    <div class="brand-name md">Corvell's<br>Entertainment</div>
  </div>
  <address class="envelope-address" style="font-style:normal">18, Lotus Garden Road<br>Colombo 01000, Sri Lanka</address>
  <div class="site">www.corvellcolombo.com</div>
  <svg class="band" width="373" height="8" viewBox="0 0 373 8">
    <polygon points="0,0 183,0 176,8 0,8" fill="var(--ink)"/>
    <polygon points="186,0 373,0 373,8 179,8" fill="var(--band-red)"/>
  </svg>
</section>

<section class="card face" aria-label="Business card front">
  <div class="brand">
    <span class="brand-dot sm"></span>
    <div class="brand-name sm">Corvell's<br>Entertainment</div>
  </div>
  <div class="card-company">
    <div class="company">CORVELL'S LIMITED</div>
    <div>18, Lotus Garden Road</div>
    <div>Colombo 01000</div>
    <div>Sri Lanka</div>
  </div>
  <div class="card-divider"></div>
  <div class="card-contact">
    <div><span class="icon-dot"></span>+ 94 11 5550142</div>
    <div><span class="icon-dot"></span>+ 94 77 5550100</div>
    <div><span class="icon-dot"></span>+ 94 11 5550100</div>
    <div><span class="icon-dot"></span>info@corvellcolombo.com</div>
    <div><span class="icon-dot"></span>www.corvellcolombo.com</div>
  </div>
  <svg class="band" width="203" height="6" viewBox="0 0 203 6">
    <polygon points="0,0 102,0 96,6 0,6" fill="var(--ink)"/>
    <polygon points="105,0 203,0 203,6 99,6" fill="var(--band-red)"/>
  </svg>
</section>

<section class="card reverse" aria-label="Business card back">
  <div class="brand">
    <span class="brand-dot sm"></span>
    <div class="brand-name sm">Corvell's<br>Entertainment</div>
  </div>
  <p class="tagline">Highest Winning Percentage In The World</p>
</section>

</body>
</html>
```